A clean crisp business card for a Landscape Construction company. Designed to be easy to read contact/ info and also be appealing/interesting, unlike a traditional business card.

Industry/Entity Type

Landscape Construction

Contact Information for Business Card

Company name : Brambleford Landscape Construction, phone number: (877) 62Vista, website:Bramblefordyards.example, Email, sales@bramblefordyards.example

Requirements
Nice to have
• Luxurious finishes/ details…. Icons or emblems next to contact info
Should not have
• Clipart or general pictures

```html
<!DOCTYPE html>
<html lang="en">
<head>
<meta charset="utf-8">
<title>Brambleford Landscape Construction – Business Card</title>
<link rel="stylesheet" href="https://fonts.googleapis.com/css2?family=Source+Sans+3:wght@400;600&display=swap">
<style>
  :root {
    --bg: #c3cfd3;
    --card: #f7f6f4;
    --green-deep: #07923f;
    --green-mid: #3fae49;
    --green-lime: #8cc63f;
    --green-pale: #cfe8c4;
    --brand-blue: #1e6ec4;
    --ink: #1c3312;
    --rule: #dde1e4;
  }
  * { box-sizing: border-box; margin: 0; padding: 0; }
  html, body { width: 1200px; height: 1200px; overflow: hidden; }
  body {
    background: var(--bg);
    font-family: "Source Sans 3", sans-serif;
    position: relative;
  }
  .card {
    position: absolute;
    width: 786px;
    height: 442px;
    background: var(--card);
    overflow: hidden;
  }
  .card--front { left: 210px; top: 113px; }
  .card--back { left: 224px; top: 653px; }
  .card__art { position: absolute; inset: 0; width: 100%; height: 100%; }

  .brand {
    position: absolute;
    color: var(--brand-blue);
    font-weight: 400;
    text-align: center;
    display: flex;
    flex-direction: column;
    align-items: center;
    line-height: 1;
  }
  .brand__dot {
    width: 34px; height: 34px; border-radius: 50%;
    background: var(--brand-blue);
    margin-bottom: 12px;
  }
  .brand__name { letter-spacing: 0.06em; text-transform: uppercase; }
  .brand__tag { text-transform: uppercase; letter-spacing: 0.3em; margin-top: 6px; }

  .card--front .brand { left: 223px; top: 150px; width: 320px; }
  .card--front .brand__name { font-size: 40px; }
  .card--front .brand__tag { font-size: 11px; }

  .card--back .brand { left: 10px; top: 60px; width: 170px; }
  .card--back .brand__dot { width: 22px; height: 22px; margin-bottom: 8px; }
  .card--back .brand__name { font-size: 21px; }
  .card--back .brand__tag { font-size: 6px; letter-spacing: 0.22em; margin-top: 4px; }

  .person__name {
    position: absolute; left: 389px; top: 80px;
    font-size: 34px; font-weight: 400; color: var(--ink);
  }
  .person__rule {
    position: absolute; left: 368px; top: 171px;
    width: 366px; height: 2px; background: var(--rule);
  }
  .person__role {
    position: absolute; left: 488px; top: 178px;
    font-size: 25px; color: var(--ink);
  }

  .contact {
    position: absolute; top: 311px; left: 0; width: 100%;
    list-style: none;
  }
  .contact__item {
    position: absolute; display: flex; align-items: center; gap: 7px;
    font-size: 13.5px; color: var(--ink);
  }
  .contact__item:nth-child(1) { left: 52px; }
  .contact__item:nth-child(2) { left: 251px; }
  .contact__item:nth-child(3) { left: 503px; }
  .contact__icon {
    width: 28px; height: 28px; border-radius: 50%;
    background: var(--ink);
    display: flex; align-items: center; justify-content: center;
  }
  .contact__icon svg { width: 16px; height: 16px; }
</style>
</head>
<body>

<section class="card card--front" aria-label="Card front">
  <svg class="card__art" viewBox="0 0 1265 712" preserveAspectRatio="none" aria-hidden="true">
    <defs>
      <linearGradient id="band" x1="0" x2="1">
        <stop offset="0" stop-color="#07923f"/>
        <stop offset="0.6" stop-color="#3fae49"/>
        <stop offset="1" stop-color="#8cc63f"/>
      </linearGradient>
      <linearGradient id="fade" x1="0" y1="0" x2="1" y2="1">
        <stop offset="0" stop-color="#cfe8c4"/>
        <stop offset="1" stop-color="#cfe8c4" stop-opacity="0"/>
      </linearGradient>
      <linearGradient id="cornerFade" x1="0" y1="0" x2="1" y2="0">
        <stop offset="0" stop-color="#cfe8c4" stop-opacity="0.2"/>
        <stop offset="1" stop-color="#cfe8c4"/>
      </linearGradient>
    </defs>
    <polygon points="40,0 165,0 240,75 180,140" fill="url(#fade)" opacity="0.7"/>
    <path d="M230,0 L280,0 Q310,45 380,47 L620,47 L720,150 L365,135 Z" fill="url(#fade)" opacity="0.6"/>
    <path d="M620,47 L900,47 Q1000,47 1080,110 L1143,186 L1100,220 Q900,220 800,160 L720,150 Z" fill="#ffffff" opacity="0.8"/>
    <path d="M706,47 L900,47 Q1000,47 1080,120 L1143,186 L950,186 Q840,186 760,100 Z" fill="url(#band)"/>
    <polygon points="1050,0 1113,0 1180,70 1150,100" fill="url(#cornerFade)" opacity="0.6"/>
    <polygon points="1113,0 1265,0 1265,150" fill="url(#band)"/>
    <polygon points="0,458 120,580 0,580" fill="url(#fade)"/>
    <path d="M0,580 L475,580 Q530,580 570,620 L660,712 L0,712 Z" fill="#ffffff"/>
    <path d="M0,614 L478,614 Q520,614 550,644 L608,712 L0,712 Z" fill="url(#band)"/>
    <polygon points="560,580 620,580 730,712 650,712" fill="url(#fade)" opacity="0.6"/>
    <path d="M640,664 L1070,664 Q1110,664 1150,712 L700,712 Z" fill="#ffffff"/>
    <polygon points="1070,560 1145,540 1265,660 1265,712 1190,712" fill="url(#cornerFade)" opacity="0.8"/>
  </svg>
  <div class="brand">
    <span class="brand__dot"></span>
    <span class="brand__name">Brambleford</span>
    <span class="brand__tag">Landscape Construction</span>
  </div>
</section>

<section class="card card--back" aria-label="Card back">
  <svg class="card__art" viewBox="0 0 1265 712" preserveAspectRatio="none" aria-hidden="true">
    <defs>
      <linearGradient id="sweep" x1="0" x2="1">
        <stop offset="0" stop-color="#ffffff"/>
        <stop offset="0.35" stop-color="#eef6e2"/>
        <stop offset="1" stop-color="#a6d35a"/>
      </linearGradient>
      <linearGradient id="band2" x1="0" x2="1">
        <stop offset="0" stop-color="#07923f"/>
        <stop offset="0.6" stop-color="#3fae49"/>
        <stop offset="1" stop-color="#8cc63f"/>
      </linearGradient>
      <linearGradient id="fade2" x1="1" y1="0" x2="0" y2="1">
        <stop offset="0" stop-color="#cfe8c4"/>
        <stop offset="1" stop-color="#cfe8c4" stop-opacity="0"/>
      </linearGradient>
    </defs>
    <path d="M0,0 L702,0 L440,262 Q380,320 320,300 L250,360 Q200,420 100,420 L0,420 Z" fill="url(#sweep)"/>
    <polygon points="600,0 702,0 440,262 380,240" fill="#b9dfa6" opacity="0.5"/>
    <path d="M0,420 L100,420 Q200,420 250,370 L0,452 Z" fill="#ffffff" opacity="0.9"/>
    <path d="M0,582 L475,582 Q530,582 570,620 L660,712 L0,712 Z" fill="#ffffff"/>
    <path d="M0,614 L478,614 Q520,614 550,644 L608,712 L0,712 Z" fill="url(#band2)"/>
    <polygon points="560,582 640,582 735,712 660,712" fill="url(#fade2)" opacity="0.6"/>
    <path d="M660,664 L1070,664 Q1110,664 1150,712 L700,712 Z" fill="#ffffff"/>
    <polygon points="1000,590 1075,570 1215,712 1140,712" fill="url(#fade2)" opacity="0.8"/>
  </svg>

  <div class="brand">
    <span class="brand__dot"></span>
    <span class="brand__name">Brambleford</span>
    <span class="brand__tag">Landscape Construction</span>
  </div>

  <h1 class="person__name">Maren Ellis Whitcombe</h1>
  <div class="person__rule"></div>
  <p class="person__role">marketing director</p>

  <ul class="contact">
    <li class="contact__item">
      <span class="contact__icon">
        <svg viewBox="0 0 16 16" fill="none" stroke="#fff" stroke-width="1.4"><rect x="2" y="4" width="12" height="8.5" rx="1"/><path d="M2.5 4.5 8 9l5.5-4.5"/></svg>
      </span>
      (555) 018 2274
    </li>
    <li class="contact__item">
      <span class="contact__icon">
        <svg viewBox="0 0 16 16" fill="none" stroke="#fff" stroke-width="1.4"><path d="M4 2.5 6 5 5 6.5c.8 1.7 2 2.9 3.5 3.5L10 9l2.5 2-1 2c-4.5 0-8.5-4-8.5-8.5Z"/></svg>
      </span>
      maren@bramblefordyards.example
    </li>
    <li class="contact__item">
      <span class="contact__icon">
        <svg viewBox="0 0 16 16" fill="none" stroke="#fff" stroke-width="1.2"><circle cx="8" cy="8" r="5.8"/><ellipse cx="8" cy="8" rx="2.4" ry="5.8"/><path d="M2.2 8h11.6M3 5h10M3 11h10"/></svg>
      </span>
      bramblefordyards.example
    </li>
  </ul>
</section>

</body>
</html>
```